Process Serving Company needs a letterhead design

Looking to have a letterhead designed for letters to attorneys advertising our business. We would like something eye catching but professional. Colors and logos are attached. Please add "Process Service and Attorney Support" near the logo or header

Target Market(s)

Attorneys

Font styles to use
Serif
Sans Serif

Colors
33a6d7
0255a3
85cae6
cee9f5
ecf7fb

```html
<!DOCTYPE html>
<html lang="en">
<head>
<meta charset="utf-8">
<title>Mesa Ridge Serve Letterhead</title>
<link href="https://fonts.googleapis.com/css2?family=Source+Sans+3:wght@400;600;700&family=Arimo:wght@700&display=swap" rel="stylesheet">
<style>
  :root {
    --sky: #33a6d7;
    --navy: #0255a3;
    --mist: #85cae6;
    --ice: #cee9f5;
    --frost: #ecf7fb;
    --ink: #3a3a3c;
    --dark: #1b1b1b;
    --backdrop: #e6e6e6;
    --paper: #ffffff;
  }
  * { box-sizing: border-box; margin: 0; padding: 0; }
  html, body { width: 1059px; height: 1200px; overflow: hidden; background: var(--backdrop); }
  .letterhead {
    position: absolute; left: 104px; top: 0;
    width: 850px; height: 1200px;
    background: linear-gradient(#ffffff 45%, #f6f6f6);
    font-family: "Source Sans 3", sans-serif;
    color: var(--ink);
  }
  .brand {
    position: absolute; left: 78px; top: 50px;
    display: flex; align-items: center; gap: 14px;
  }
  .brand-square { width: 56px; height: 56px; background: var(--ice); }
  .brand-name {
    font-family: "Source Sans 3", sans-serif;
    font-weight: 400; font-size: 30px; color: var(--sky);
    letter-spacing: 0.5px;
  }
  .salutation {
    position: absolute; left: 78px; top: 290px;
    font-family: "Arimo", sans-serif; font-weight: 700; font-size: 18.5px; color: var(--dark);
  }
  .letter-body {
    position: absolute; left: 78px; top: 326px; width: 695px;
    font-size: 17.4px; line-height: 22.3px; text-align: justify;
  }
  .letter-body p { margin-bottom: 22.3px; }
  .signature {
    position: absolute; left: 78px; top: 905px; width: 135px; height: 65px;
    background: linear-gradient(90deg, #dcdcdc, #eeeeee);
    border-radius: 4px;
  }
  .footer-contact {
    position: absolute; left: 78px; top: 1154px;
    font-size: 11.5px; line-height: 15px; color: var(--dark);
  }
  .contact-line { display: flex; align-items: center; gap: 4px; font-size: 12.5px; }
  .contact-line svg { width: 11px; height: 11px; fill: var(--navy); }
  .contact-line .gap { margin-left: 6px; }
  .footer-web {
    position: absolute; right: 78px; top: 1169px;
    font-size: 13.5px; color: var(--dark);
  }
  .footer-web strong { color: var(--navy); font-weight: 700; }
</style>
</head>
<body>
<main class="letterhead">
  <header class="brand">
    <div class="brand-square"></div>
    <div class="brand-name">Mesa Ridge Serve</div>
  </header>

  <h1 class="salutation">Dear Mr. Dalton,</h1>

  <section class="letter-body">
    <p>Lorem Ipsum is simply dummy text of the printing and typesetting industry. Lorem Ipsum has been the industry's standard dummy text ever since the 1500s, when an unknown printer took a galley of type and scrambled it to make a type specimen book. It has survived not only five centuries, but also the leap into electronic typesetting, remaining essentially unchanged.</p>
    <p>The standard chunk of Lorem Ipsum used since the 1500s is reproduced below for those interested. Sections 1.10.32 and 1.10.33 from "de Finibus Bonorum et Malorum" by Cicero are also reproduced in their exact original form, accompanied by English versions from the 1914 translation by H. Rackham</p>
    <p>Lorem Ipsum is simply dummy text of the printing and typesetting industry. Lorem Ipsum has been the industry's standard dummy text ever since the 1500s, when an unknown printer took a galley of type and scrambled it to make a type specimen book. It has survived not only five centuries, but also the leap into electronic typesetting, remaining essentially unchanged. It was popularised in the</p>
    <p>The standard chunk of Lorem Ipsum used since the 1500s is reproduced below for those interested. Sections 1.10.32 and 1.10.33 from "de Finibus Bonorum et Malorum" by Cicero are also reproduced in their exact original form, accompanied by English versions from the 1914 translation by H. Rackham</p>
    <p>The standard chunk of Lorem Ipsum used since the 1500s is reproduced below for those interested. Sections 1.10.32 and 1.10.33 from "de Finibus Bonorum et Malorum" by Cicero are</p>
  </section>

  <div class="signature" role="img" aria-label="Handwritten signature of the sender"></div>

  <footer>
    <div class="footer-contact">
      <div>4120 E Palo Verde Rd #210 Phoenix AZ 85018</div>
      <div class="contact-line">
        <svg viewBox="0 0 12 12" aria-hidden="true"><path d="M2.5 0.5l2 2.5-1 1.2c.6 1.5 1.8 2.7 3.3 3.3l1.2-1 2.5 2-1 2.2C5 10.5 1.5 7 0.3 1.5z"/></svg>
        <span>602-555-0148</span>
        <svg class="gap" viewBox="0 0 12 12" aria-hidden="true"><path d="M3 1h6v3H3zM1 5h10v5H9V8H3v2H1zM4 9h4v3H4z"/></svg>
        <span>602-555-0172</span>
        <svg class="gap" viewBox="0 0 12 12" aria-hidden="true"><path d="M0 2.5h12v7H0zM1 3.3l5 3.6 5-3.6v0.9L6 7.8 1 4.2z" fill-rule="evenodd"/></svg>
        <span style="font-size:11.5px">info@MesaRidgeServe.com</span>
      </div>
    </div>
    <div class="footer-web">www.<strong>MesaRidgeServe</strong>.com</div>
  </footer>
</main>
</body>
</html>
```